Vosley Insurance Stationery Design Project

We need a stationery design for business cards, letterhead and envelopes.

Please refer to attached brief for further information.

Industry/Entity Type

Business

```html
<!DOCTYPE html>
<html lang="en">
<head>
<meta charset="utf-8">
<title>Vosley Insurance – Business Card</title>
<link rel="stylesheet" href="https://fonts.googleapis.com/css2?family=Source+Sans+3:wght@400;600;700&display=swap">
<style>
  :root {
    --backdrop: #a8801c;
    --card: #ffffff;
    --panel: #f9f9f9;
    --rule: #c9c9c9;
    --orange: #f47a27;
    --grey: #c6c6c6;
    --grey-text: #a9a9a9;
    --ink: #2b2b2b;
    --navy: #003250;
  }
  * { margin: 0; padding: 0; box-sizing: border-box; }
  html, body { width: 1200px; height: 686px; overflow: hidden; }
  body {
    background: var(--backdrop);
    font-family: "Source Sans 3", sans-serif;
    position: relative;
  }
  .card { position: absolute; width: 524px; height: 300px; }

  /* Front */
  .card--front { left: 62px; top: 139px; background: var(--card); }
  .card--front .panel {
    position: absolute; inset: 17px 20px 17px 18px;
    background: var(--panel); border: 1px solid var(--rule);
  }
  .brand {
    position: absolute; left: 18px; top: 28px;
    display: flex; align-items: center; gap: 8px;
  }
  .brand__dot { width: 16px; height: 16px; border-radius: 50%; background: var(--orange); }
  .brand__name { font-size: 23px; font-weight: 600; color: var(--grey); line-height: 1; }

  .details {
    position: absolute; right: 22px; top: 27px;
    text-align: right; color: var(--ink);
  }
  .details__person { font-size: 16px; line-height: 20px; margin-bottom: 8px; }
  .details__name { color: var(--orange); font-weight: 700; }
  .details__role { color: #666; font-weight: 600; font-size: 13px; border-left: 1px solid #666; padding-left: 6px; margin-left: 4px; }
  .details__address { font-size: 13.5px; line-height: 16.5px; margin-bottom: 10px; }
  .details__contact { font-size: 13.5px; line-height: 19px; }
  .details__contact b { color: var(--orange); font-weight: 700; }
  .details__contact span + span { margin-left: 12px; }
  .details__tagline { font-size: 12.5px; font-weight: 700; color: var(--grey-text); margin-top: 4px; margin-bottom: 10px; }
  .details__legal { font-size: 12px; line-height: 17px; color: var(--orange); }

  /* Back */
  .card--back { left: 617px; top: 211px; background: var(--navy); }
  .card--back .panel {
    position: absolute; inset: 17px 20px 17px 18px; background: var(--panel);
  }
  .mark {
    position: absolute; left: 142px; top: 50px;
    display: flex; align-items: center; gap: 12px;
  }
  .mark__dot { width: 46px; height: 46px; border-radius: 50%; background: var(--orange); }
  .mark__name { font-size: 54px; font-weight: 600; color: var(--grey); line-height: 1; }
  .website {
    position: absolute; left: 0; right: 0; top: 215px;
    text-align: center; font-size: 13px; font-weight: 700; color: var(--grey-text);
  }
  .website b { color: var(--orange); }
</style>
</head>
<body>
  <section class="card card--front" aria-label="Business card front">
    <div class="panel">
      <div class="brand">
        <span class="brand__dot"></span>
        <span class="brand__name">Vosley Insurance</span>
      </div>
      <div class="details">
        <p class="details__person"><span class="details__name">Dean Vosley</span><span class="details__role">Director</span></p>
        <p class="details__address">Level 4, 18 Harlow St<br>Eastbridge NSW 2061<br>PO Box 417 Eastbridge NSW 2058</p>
        <p class="details__contact"><span><b>T</b> : (02) 5550 1834</span><span><b>F</b> : (02) 5550 1835</span></p>
        <p class="details__contact"><span><b>M</b> : 0400 555 218</span><span><b>E</b> : dvosley@vmail.net.au</span></p>
        <p class="details__tagline">Business and Life Insurance Brokers and Advisers</p>
        <p class="details__legal">Authorised Representative No. 402718<br>
          Clearline Advice Partners Pty Limited AFSL 251930 Clearline Advice<br>
          Financial Services Pty Ltd and its advisers are members of Harbourline Financial<br>
          Advisers and Authorised Representatives of Northgate Advice Pty Ltd AFSL 274415</p>
      </div>
    </div>
  </section>

  <section class="card card--back" aria-label="Business card back">
    <div class="panel">
      <div class="mark">
        <span class="mark__dot"></span>
        <span class="mark__name">Vosley</span>
      </div>
      <p class="website">www.<b>vosleyinsurance</b>.com.au</p>
    </div>
  </section>
</body>
</html>
```